NZ First of it's kind solutions directory and marketplace for busy Mums needs a business card design

We need a business card design for our new nationwide business in NZ (long term plans to go global). We provide solutions to the everyday challenges that busy Mums face by connecting them with quality communities and suppliers of carefully selected, relevant products and services. We sell direct via our online marketplace. The final design should communicate our values of inclusivity, quality and smart solutions. Colours should incorporate our logo colour palette of #477077 and #6ba8b2. Our website is at https://www.brightnestmums.example

Target Market(s)

busy Mums, Age 28 – 50, female, income over $100K, location main centres NZ primarily but NZ wide. Is likely juggling work or career with a young family. Probably had hobbies which have fallen by the wayside.
-Wants to succeed in her chosen career without compromising on family life
-to successfully juggle her career without feeling like she is compromising her children
- Is time poor, something always has to give and it’s generally her health (she’ll stay up late, get stressed)
- probably ex corporate or professional career. Has discretional income

Industry/Entity Type

Business

Contact Information for Business Card

Lena Forbisher, Founder, BrightNestMums.example (Strapline Tap; Gather; Sorted), 47 Kowhai Terrace, Ellerslie, Auckland 1051, New Zealand. Mob: 021 483 517 Ph: +64 (0)9 571 4860

Font styles to use
Other font styles liked:
• Raleway, and/or Architects Daughter

Colors
00a990
33b8a4
86cfc6
cfeae6

Requirements
Must have
• the above details, streamline. the logo and colours associated with those logos
Should not have
• foil or metallic colours

```html
<!DOCTYPE html>
<html lang="en">
<head>
<meta charset="utf-8">
<title>BrightNestMums – Business Card</title>
<link rel="stylesheet" href="https://fonts.googleapis.com/css2?family=Maven+Pro:wght@500;700&family=Roboto+Condensed:ital,wght@0,400;1,400&display=swap">
<style>
  :root {
    --backdrop: #e6e6e6;
    --card: #f7f7f7;
    --brand-dark: #477077;
    --brand-deep: #3d5c63;
    --brand-light: #6ba8b2;
    --ink: #3a3a3a;
    --ink-soft: #4a4a4a;
    --white: #ffffff;
  }
  * { box-sizing: border-box; margin: 0; padding: 0; }
  html, body {
    width: 1200px; height: 576px; overflow: hidden;
    background: var(--backdrop);
  }
  .canvas { position: relative; width: 1200px; height: 576px; }

  .card {
    position: absolute;
    top: 138px;
    width: 484px; height: 294px;
    background: var(--card);
    border-radius: 10px;
    overflow: hidden;
  }
  .card--front { left: 82px; }
  .card--back { left: 602px; }

  .feature-disc {
    position: absolute;
    width: 204px; height: 204px;
    border-radius: 50%;
    background: var(--brand-deep);
  }
  .card--front .feature-disc { left: 283px; top: 96px; }
  .card--back .feature-disc { left: 277px; top: 78px; }

  .brand {
    position: absolute;
    display: flex; flex-direction: column;
  }
  .card--front .brand { left: 30px; top: 128px; }
  .card--back .brand { left: 27px; top: 28px; }

  .brand-row { display: flex; align-items: center; gap: 8px; }
  .brand-dot {
    width: 22px; height: 22px; border-radius: 50%;
    background: var(--brand-dark);
  }
  .brand-name {
    font-family: "Maven Pro", sans-serif;
    font-weight: 700;
    color: var(--brand-dark);
    letter-spacing: -0.5px;
    line-height: 1;
  }
  .card--front .brand-name { font-size: 27px; }
  .card--back .brand-name { font-size: 28px; }

  .strapline {
    font-family: "Roboto Condensed", sans-serif;
    font-size: 10px;
    letter-spacing: 3.4px;
    color: var(--ink-soft);
    text-transform: uppercase;
    margin-top: 7px;
  }
  .card--front .strapline { padding-left: 30px; }
  .strapline .divider { color: var(--brand-light); margin: 0 3px; }

  .address {
    position: absolute; left: 26px; top: 160px;
    font-family: "Roboto Condensed", sans-serif;
    font-size: 12px; line-height: 18px;
    color: var(--ink);
    font-style: normal;
  }
  .contact-list {
    position: absolute; left: 26px; top: 205px;
    list-style: none;
    font-family: "Roboto Condensed", sans-serif;
    font-size: 12px; line-height: 18px;
    color: var(--ink);
  }
  .contact-list li { display: flex; align-items: center; gap: 8px; }
  .contact-list svg { width: 10px; height: 10px; fill: var(--brand-light); flex: none; }

  .person {
    position: absolute; left: 300px; top: 215px; width: 160px;
    text-align: center; color: var(--white);
  }
  .person-name {
    font-family: "Maven Pro", sans-serif;
    font-weight: 700; font-size: 18px; line-height: 1.1;
  }
  .person-role {
    font-family: "Roboto Condensed", sans-serif;
    font-style: italic; font-size: 12px;
  }
</style>
</head>
<body>
<div class="canvas">

  <section class="card card--front" aria-label="Card front">
    <div class="feature-disc"></div>
    <div class="brand">
      <div class="brand-row">
        <span class="brand-dot"></span>
        <span class="brand-name">BrightNestMums</span>
      </div>
      <p class="strapline">Tap<span class="divider">|</span>Gather<span class="divider">|</span>Sorted</p>
    </div>
  </section>

  <section class="card card--back" aria-label="Card back">
    <div class="feature-disc"></div>
    <div class="brand">
      <span class="brand-name">BrightNestMums</span>
      <p class="strapline">Tap<span class="divider">|</span>Gather<span class="divider">|</span>Sorted</p>
    </div>

    <address class="address">
      47 Kowhai Terrace, Ellerslie,<br>
      Auckland 1051, New Zealand
    </address>

    <ul class="contact-list">
      <li>
        <svg viewBox="0 0 10 10" aria-hidden="true"><rect x="2.5" y="0" width="5" height="10" rx="1"/><rect x="3.5" y="1.2" width="3" height="6" fill="#f7f7f7"/></svg>
        021 483 517
      </li>
      <li>
        <svg viewBox="0 0 10 10" aria-hidden="true"><path d="M0 3 Q5 0 10 3 L9 4.5 L7 4 L7 3 Q5 2.3 3 3 L3 4 L1 4.5 Z"/><rect x="1.5" y="5" width="7" height="5" rx="1"/></svg>
        +64 (0)9 571 4860
      </li>
      <li>
        <svg viewBox="0 0 10 10" aria-hidden="true"><rect x="0" y="2" width="10" height="6.5"/><path d="M0 2 L5 6 L10 2" fill="none" stroke="#f7f7f7" stroke-width="1"/></svg>
        www.BrightNestMums.example
      </li>
      <li>
        <svg viewBox="0 0 10 10" aria-hidden="true"><circle cx="5" cy="5" r="5"/><path d="M0 5 H10 M5 0 V10 M5 0 Q2 5 5 10 M5 0 Q8 5 5 10" fill="none" stroke="#f7f7f7" stroke-width="0.7"/></svg>
        lena@brightnestmums.example
      </li>
    </ul>

    <div class="person">
      <p class="person-name">Lena Forbisher</p>
      <p class="person-role">Founder</p>
    </div>
  </section>

</div>
</body>
</html>
```